Logo, Web and Mobile Designs for enterprise social media platform

All the details are in the attached document, please start reading the scope document first which explains what is this project about and the details about the needed deliverables, after that please read the UI_Requirements document which will detail what is expected regarding the coded web version since this is a coded contest, it is very important that you meet the UI requirements or suggest something else but we will need to agree first before working on the coded version

Good Luck

Target Market(s)

Enterprise Social Media

Industry/Entity Type

Media

Coding

Coded - Design and coding required

Number of Pages Required

5+ page

Font styles to use
Sans Serif

Requirements
Must have
• All the must haves are listed in the scope document so please check before you start

```html
<!DOCTYPE html>
<html lang="en">
<head>
<meta charset="utf-8">
<title>Teamora – Events</title>
<link href="https://fonts.googleapis.com/css2?family=Marcellus&family=Raleway:wght@400;500;600;700&family=Open+Sans:wght@400;600&display=swap" rel="stylesheet">
<style>
:root{
  --blue-top:#2d95dc;
  --blue-bottom:#1769b3;
  --blue:#1a7fd0;
  --link:#1f7cc4;
  --orange:#f7a20f;
  --text:#4a4a4a;
  --muted:#8c8c8c;
  --line:#dcdcdc;
  --panel:#f2f2f2;
  --footer-top:#255a92;
  --footer-bottom:#173f6c;
}
*{box-sizing:border-box;margin:0;padding:0}
html,body{width:790px;height:1200px;overflow:hidden;background:#fff}
body{position:relative;font-family:"Raleway",sans-serif;color:var(--text)}
.abs{position:absolute}

.site-header{left:0;top:0;width:790px;height:72px;background:linear-gradient(var(--blue-top),var(--blue-bottom))}
.brand{left:92px;top:20px;font-family:"Marcellus",serif;font-size:26px;color:#fff}
.nav-item{top:0;height:72px;display:flex;flex-direction:column;align-items:center;justify-content:center;color:#fff;font-size:11px;transform:translateX(-50%);gap:6px}
.nav-item svg{width:18px;height:18px;fill:#fff}
.nav-sep{top:0;width:1px;height:72px;background:rgba(255,255,255,.2)}

.hero{left:0;top:72px;width:790px;height:244px;background:radial-gradient(circle at 60% 40%,#8a3a1e 0%,#4a1f14 45%,#1e1410 100%)}
.hero-kicker{left:94px;top:162px;font-weight:700;font-size:17px;color:#fff}
.hero-title{left:94px;top:182px;font-weight:700;font-size:28px;color:#fff;letter-spacing:.5px}
.dots{left:364px;top:290px;display:flex;gap:3px}
.dots span{width:13px;height:13px;border-radius:50%;background:#fff}

.box{border:1px solid var(--line);background:#fff}
.profile{left:90px;top:334px;width:135px;height:192px}
.profile-head{height:50px;background:var(--panel);display:flex;align-items:center;padding-left:14px;gap:8px}
.avatar{width:30px;height:30px;border-radius:50%;background:linear-gradient(#9aa3ab,#5d666e)}
.profile-head b{display:block;font-weight:500;font-size:10px}
.profile-head small{font-size:7.5px;color:var(--muted)}
.menu{list-style:none;margin-top:6px}
.menu li{height:22px;border-bottom:1px solid #ececec;display:flex;align-items:center;padding-left:18px;gap:7px;font-size:8.5px}
.menu li:last-child{border:none}
.menu svg{width:11px;height:11px;fill:var(--blue)}

.side-head{height:25px;background:linear-gradient(#2fa8f0,#1986d8);color:#fff;font-size:11px;padding-left:17px;display:flex;align-items:center}
.latest{left:90px;top:534px;width:135px;height:346px}
.featured{left:90px;top:891px;width:135px;height:199px}
.thumb{position:absolute;left:13px;width:113px}
.ev-title{position:absolute;left:15px;font-size:10px}
.ev-text{position:absolute;left:15px;width:110px;font-family:"Open Sans",sans-serif;font-size:6px;line-height:10px;color:var(--muted)}
.ev-date{position:absolute;left:15px;font-size:7.5px}
.play{position:absolute;width:18px;height:18px;border-radius:50%;background:#111;display:flex;align-items:center;justify-content:center}
.play::after{content:"";border-left:6px solid #fff;border-top:4px solid transparent;border-bottom:4px solid transparent;margin-left:2px}

.compose{left:238px;top:334px;width:455px;height:84px}
.section-title{position:absolute;left:16px;font-size:13px;font-weight:500;color:#555}
.ph-avatar{left:16px;top:35px;width:33px;height:27px;background:#ddd}
.input{left:58px;top:35px;width:226px;height:19px;border:1px solid var(--line);font-size:7px;color:#666;padding:5px 7px}
.btn{height:18px;color:#fff;font-size:8px;display:flex;align-items:center;justify-content:center}
.btn-blue{left:302px;top:35px;width:58px;background:var(--blue)}
.btn-orange{left:364px;top:35px;width:80px;background:var(--orange)}

.feed{left:238px;top:428px;width:455px;height:662px}
.timeline{left:21px;top:52px;width:1px;height:396px;background:var(--line)}
.num{position:absolute;left:13px;width:17px;height:17px;border-radius:50%;color:#fff;font-size:8px;display:flex;align-items:center;justify-content:center}
.num.on{background:var(--blue)}
.num.off{background:#b5b5b5}
.post-avatar{position:absolute;width:37px;height:32px;background:linear-gradient(#b08a6e,#5a4230)}
.post-title{position:absolute;font-size:11px;color:var(--link)}
.post-text{position:absolute;width:350px;font-family:"Open Sans",sans-serif;font-size:6.5px;line-height:10px;color:var(--muted)}
.post-meta{position:absolute;display:flex;align-items:center;gap:6px;font-size:7px}
.tag{display:flex;align-items:center;gap:4px;background:#ececec;border-radius:9px;padding:1px 5px 1px 1px;font-size:6.5px}
.tag i{width:14px;height:14px;border-radius:50%;background:#8a5a3c}
.media{position:absolute}
.actions{position:absolute;display:flex;align-items:center;font-size:8.5px;color:#666;gap:14px}
.actions svg{width:10px;height:10px;fill:#555;vertical-align:-1px;margin-right:3px}
.stats{margin-left:18px;display:flex;gap:13px;font-size:7.5px;color:var(--muted)}
.more{left:67px;top:620px;width:108px;height:22px;background:var(--orange)}

.site-footer{left:0;top:1122px;width:790px;height:78px;background:linear-gradient(var(--footer-top),var(--footer-bottom))}
.foot-links{left:93px;top:23px;display:flex;gap:17px;color:#fff;font-size:10px}
.copy{left:93px;top:43px;color:#fff;font-size:7.5px;font-family:"Open Sans",sans-serif}
.social{left:620px;top:25px;display:flex;gap:8px}
.social span{width:12px;height:12px;border-radius:50%;background:#fff}
</style>
</head>
<body>

<header class="abs site-header">
  <div class="abs brand">Teamora</div>
  <div class="abs nav-sep" style="left:334px"></div>
  <div class="abs nav-sep" style="left:428px"></div>
  <div class="abs nav-sep" style="left:499px"></div>
  <div class="abs nav-sep" style="left:570px"></div>
  <a class="abs nav-item" style="left:311px"><svg viewBox="0 0 20 20"><circle cx="10" cy="10" r="10"/><text x="10" y="15" text-anchor="middle" font-size="14" font-weight="700" fill="#1f78c4" font-family="Arial">?</text></svg>About</a>
  <a class="abs nav-item" style="left:382px"><svg viewBox="0 0 20 20"><path d="M19 1 1 9l6 2 2 7 3-5 5 3z"/></svg>Post New Event</a>
  <a class="abs nav-item" style="left:465px"><svg viewBox="0 0 20 20"><rect x="7" y="1" width="6" height="5"/><rect x="1" y="13" width="5" height="5"/><rect x="7.5" y="13" width="5" height="5"/><rect x="14" y="13" width="5" height="5"/><path d="M9.3 6h1.4v3H17v4h-1.4v-2.6H10.7V13H9.3v-2.6H4.4V13H3V9h6.3z"/></svg>Share Now</a>
  <a class="abs nav-item" style="left:535px"><svg viewBox="0 0 20 20"><circle cx="6" cy="5" r="3"/><circle cx="14" cy="5" r="3"/><circle cx="10" cy="9" r="3"/><path d="M0 14c0-4 12-4 12 0v2H0zM8 14c0-4 12-4 12 0v2H8z"/></svg>Participate</a>
  <a class="abs nav-item" style="left:602px"><svg viewBox="0 0 20 20"><circle cx="10" cy="6" r="5"/><path d="M1 19c0-8 18-8 18 0z"/></svg>Members</a>
</header>

<section class="abs hero" role="img" aria-label="Photo of friends toasting with glasses of drinks over a candlelit table"></section>
<div class="abs hero-kicker">MAURIS VEL LACUS VITAE FELIS</div>
<div class="abs hero-title">VESTIBULUM VOLUTPA</div>
<div class="abs dots"><span></span><span></span><span></span><span></span></div>

<aside class="abs box profile">
  <div class="profile-head"><div class="avatar" role="img" aria-label="User profile photo"></div><div><b>Username</b><small>Edit Profile</small></div></div>
  <ul class="menu">
    <li><svg viewBox="0 0 12 12"><circle cx="6" cy="6" r="6"/><path d="M5 2.5h2v2.5h2.5v2H7v2.5H5V7H2.5V5H5z" fill="#fff"/></svg>Add Events</li>
    <li><svg viewBox="0 0 12 12"><path d="M4 1h1.6v5H9c2 0 2 2 2 3v2H4L1 7l1-1 2 1.5z"/></svg>Subscribe Events</li>
    <li><svg viewBox="0 0 12 12"><path d="M7 1l5 4-5 4V6.5C3 6.5 1.5 8 0 11c0-5 3-7.5 7-7.5z"/></svg>Post an Events</li>
    <li><svg viewBox="0 0 12 12"><path d="M2 0h6l3 3v9H2zm1.5 5h6v1h-6zm0 2h6v1h-6zm0 2h6v1h-6z"/></svg>Latest Feeds</li>
    <li><svg viewBox="0 0 12 12"><circle cx="3.5" cy="3" r="2"/><circle cx="8.5" cy="3" r="2"/><path d="M0 9c0-3 7-3 7 0v1H0zm5 0c0-3 7-3 7 0v1H5z"/></svg>Participate</li>
    <li><svg viewBox="0 0 12 12"><circle cx="6" cy="6" r="4"/><rect x="5" y="0" width="2" height="12"/><rect x="0" y="5" width="12" height="2"/><circle cx="6" cy="6" r="1.6" fill="#fff"/></svg>More Featured</li>
  </ul>
</aside>

<aside class="abs box latest">
  <div class="side-head">Latest Events</div>
  <div class="thumb" style="top:35px;height:65px;background:linear-gradient(#c8662a,#8c1f4a 60%,#3a0f2a)" role="img" aria-label="Row of pink cocktails on a lit bar"></div>
  <div class="ev-title" style="top:107px">Mauris vel lacus vitae</div>
  <p class="ev-text" style="top:121px">felis vestibulum volutpat E eu imperdiet ac nisl Cum sociis natoque penatibus et magnis dis parturient montes nascetur ridiculus mus In iaculis facilisis massa</p>
  <div class="ev-date" style="top:174px">Posted 2 days ago</div>
  <div class="thumb" style="top:196px;height:65px;background:linear-gradient(#3a58d8,#1a2a8a 60%,#0d1550)" role="img" aria-label="Concert crowd with raised hands under blue stage lights"></div>
  <div class="ev-title" style="top:270px">Mauris vel lacus vitae</div>
  <p class="ev-text" style="top:282px">felis vestibulum volutpat E eu imperdiet ac nisl Cum sociis natoque penatibus et magnis dis parturient montes nascetur ridiculus</p>
  <div class="ev-date" style="top:324px">Posted 2 days ago</div>
</aside>

<aside class="abs box featured">
  <div class="side-head">Featured Event Video</div>
  <div class="thumb" style="top:34px;height:68px;background:linear-gradient(135deg,#d9a67a,#6a8fb0)" role="img" aria-label="Video still of friends laughing together"><span class="play" style="left:47px;top:25px"></span></div>
  <div class="thumb" style="top:110px;height:69px;background:linear-gradient(135deg,#d8b08c,#4f7fb8)" role="img" aria-label="Video still of friends celebrating"><span class="play" style="left:47px;top:25px"></span></div>
</aside>

<section class="abs box compose">
  <h2 class="section-title" style="top:12px">Post a New Event</h2>
  <div class="abs ph-avatar"></div>
  <div class="abs input">type event name</div>
  <div class="abs btn btn-blue">Post Now</div>
  <div class="abs btn btn-orange">Subscribe Event</div>
</section>

<section class="abs box feed">
  <h2 class="section-title" style="top:14px">Recent Posted Events</h2>
  <div class="abs timeline"></div>

  <span class="num on" style="top:164px;top:36px">1</span>
  <div class="post-avatar" style="left:35px;top:39px" role="img" aria-label="Member photo"></div>
  <div class="post-title" style="left:76px;top:37px">Mauris vel lacus vitae</div>
  <p class="post-text" style="left:76px;top:53px">Mauris vel lacus vitae felis vestibulum volutpat E eu imperdiet ac nisl Cum sociis natoque penatibus et magnis dis parturient montes nascetur ridiculus mus In iaculis facilisis massa</p>
  <div class="post-meta" style="left:76px;top:75px">Posted 2 days ago<span class="tag"><i></i>Nadia Coren ✖</span></div>
  <div class="media" style="left:80px;top:98px;width:340px;height:89px;background:linear-gradient(90deg,#6a4a3a,#c87a4a 40%,#7a7a8a)" role="img" aria-label="Crowd at an outdoor food market"></div>
  <div class="actions" style="left:84px;top:194px"><span><svg viewBox="0 0 10 10"><path d="M0 4h2v6H0zm3 0 2-4c1 0 1.5.6 1.2 2L6 4h3l-1 6H3z"/></svg>Like</span><span><svg viewBox="0 0 10 10"><path d="M0 1h6v1H1v7h7V5h1v5H0zm8-1 2 2-5 5H3V5z"/></svg>Comment</span><span><svg viewBox="0 0 10 10"><circle cx="8" cy="2" r="2"/><circle cx="2" cy="5" r="2"/><circle cx="8" cy="8" r="2"/><path d="M2 5 8 2m-6 3 6 3" stroke="#555"/></svg>Share</span><span class="stats"><span>470k Likes</span><span>62k Comments</span><span>20 Shares</span></span></div>

  <span class="num off" style="top:228px">2</span>
  <div class="post-avatar" style="left:35px;top:235px" role="img" aria-label="Member photo"></div>
  <div class="post-title" style="left:76px;top:232px">Donec dictum lectus non odio</div>
  <p class="post-text" style="left:76px;top:249px">Mauris vel lacus vitae felis vestibulum volutpat E eu imperdiet ac nisl Cum sociis natoque penatibus et magnis dis parturient montes nascetur ridiculus mus In iaculis facilisis massa</p>
  <div class="post-meta" style="left:76px;top:270px">Posted 2 days ago<span class="tag"><i></i>Nadia Coren ✖</span></div>
  <div class="media" style="left:80px;top:295px;width:159px;height:94px;background:linear-gradient(135deg,#9aa0a8,#3a3f48)" role="img" aria-label="Video still of a silver catering dish"><span class="play" style="left:70px;top:38px"></span></div>
  <div class="media" style="left:244px;top:295px;width:160px;height:94px;background:linear-gradient(135deg,#f2e6c8,#c9a86a)" role="img" aria-label="Video still of champagne glasses on a banquet table"><span class="play" style="left:70px;top:38px"></span></div>
  <div class="actions" style="left:84px;top:396px"><span><svg viewBox="0 0 10 10"><path d="M0 4h2v6H0zm3 0 2-4c1 0 1.5.6 1.2 2L6 4h3l-1 6H3z"/></svg>Like</span><span><svg viewBox="0 0 10 10"><path d="M0 1h6v1H1v7h7V5h1v5H0zm8-1 2 2-5 5H3V5z"/></svg>Comment</span><span><svg viewBox="0 0 10 10"><circle cx="8" cy="2" r="2"/><circle cx="2" cy="5" r="2"/><circle cx="8" cy="8" r="2"/><path d="M2 5 8 2m-6 3 6 3" stroke="#555"/></svg>Share</span><span class="stats"><span>470k Likes</span><span>62k Comments</span><span>20 Shares</span></span></div>

  <span class="num off" style="top:430px">3</span>
  <div class="post-avatar" style="left:37px;top:432px" role="img" aria-label="Member photo"></div>
  <div class="post-title" style="left:78px;top:429px">Donec dictum lectus non odio</div>
  <p class="post-text" style="left:78px;top:446px">Mauris vel lacus vitae felis vestibulum volutpat E eu imperdiet ac nisl Cum sociis natoque penatibus et magnis dis parturient montes nascetur ridiculus mus In iaculis facilisis massa</p>
  <div class="post-meta" style="left:78px;top:468px">Posted 2 days ago<span class="tag"><i></i>Nadia Coren ✖</span></div>
  <div class="media" style="left:82px;top:493px;width:340px;height:88px;background:linear-gradient(90deg,#3a4aa8,#c83a9a 50%,#8a5ad8)" role="img" aria-label="Banquet hall with chairs under purple lighting"></div>
  <div class="actions" style="left:86px;top:588px"><span><svg viewBox="0 0 10 10"><path d="M0 4h2v6H0zm3 0 2-4c1 0 1.5.6 1.2 2L6 4h3l-1 6H3z"/></svg>Like</span><span><svg viewBox="0 0 10 10"><path d="M0 1h6v1H1v7h7V5h1v5H0zm8-1 2 2-5 5H3V5z"/></svg>Comment</span><span><svg viewBox="0 0 10 10"><circle cx="8" cy="2" r="2"/><circle cx="2" cy="5" r="2"/><circle cx="8" cy="8" r="2"/><path d="M2 5 8 2m-6 3 6 3" stroke="#555"/></svg>Share</span><span class="stats"><span>470k Likes</span><span>62k Comments</span><span>20 Shares</span></span></div>

  <div class="abs btn more">VIEW MORE POSTS</div>
</section>

<footer class="abs site-footer">
  <nav class="abs foot-links"><span>About</span><span>Post New Event</span><span>Share Now</span><span>Participate</span><span>Members</span></nav>
  <div class="abs copy">© 2015 Company Name &nbsp;All right reserved &nbsp;Term of Use</div>
  <div class="abs social"><span></span><span></span><span></span><span></span></div>
</footer>

</body>
</html>
```